Tall fern bicycle rental

would like to have a bicycle rental website that has the ability to have a calender and be able to sign a liability waiver and pay all on line, We rent fat tire vorn bicycles

```html
<!DOCTYPE html>
<html lang="en">
<head>
<meta charset="utf-8">
<title>Tall Fern Bicycle Rental</title>
<link rel="stylesheet" href="https://fonts.googleapis.com/css2?family=Lato:wght@400;700;900&family=Orbitron:wght@900&display=swap">
<style>
:root{
  --blue:#1e8fd6;
  --blue-dark:#0f6fae;
  --navy:#124e7c;
  --ink:#222;
  --muted:#555;
  --light:#eeeeee;
  --lighter:#e6e6e6;
  --footer:#262626;
  --white:#fff;
  --display:'Orbitron',sans-serif;
  --body:'Lato',sans-serif;
}
*{margin:0;padding:0;box-sizing:border-box}
html,body{width:1200px;height:4942px;overflow:hidden}
body{position:relative;font-family:var(--body);color:var(--ink);background:var(--white)}
.abs{position:absolute}
.display{font-family:var(--display);font-weight:900;text-transform:uppercase;letter-spacing:2px}
.section-title{position:absolute;left:0;width:1200px;text-align:center;color:var(--blue);font-size:32px;line-height:46px}
.btn{position:absolute;display:flex;align-items:center;justify-content:center;font-weight:700;text-transform:uppercase;color:var(--white);background:var(--blue);font-size:15px}
.btn.dark{background:#111;font-size:14px}

/* hero */
.hero{position:absolute;left:0;top:0;width:1200px;height:868px;background:linear-gradient(160deg,#6f7378 0%,#9aa1a6 40%,#d9dee2 75%,#eef1f3 100%)}
.hero-photo{position:absolute;inset:0}
.hero-panel{position:absolute;left:0;top:0;width:590px;height:737px;background:rgba(40,42,45,.72);clip-path:polygon(0 0,100% 0,100% 100%,0 100%)}
.hero-panel::after{content:"";position:absolute;left:0;top:0;width:100%;height:280px;background:rgba(20,20,22,.35);clip-path:polygon(0 0,100% 0,0 100%)}
.brand{position:absolute;left:73px;top:40px;width:190px;text-align:center;color:var(--white)}
.brand-mark{width:60px;height:60px;border-radius:50%;background:var(--white);margin:0 auto 8px}
.brand-name{font-size:26px;font-weight:900;line-height:28px;text-transform:uppercase}
.brand-sub{font-size:11px;font-weight:700;letter-spacing:2px;text-transform:uppercase}
.brand-tag{font-size:7px;letter-spacing:.5px;text-transform:uppercase;margin-top:2px}
.nav{position:absolute;left:326px;top:90px;display:flex;gap:0}
.nav a{display:block;height:29px;line-height:29px;color:var(--white);font-size:13px;text-transform:uppercase;text-decoration:none;padding:0 18px;margin-right:12px}
.nav a.active{background:#111}
.socials{position:absolute;left:826px;top:38px;display:flex;gap:16px}
.socials span{width:18px;height:18px;border-radius:50%;background:var(--white);opacity:.9}
.login{left:1037px;top:35px;width:88px;height:34px;font-size:13px}
.hero-title{position:absolute;left:73px;top:358px;color:var(--white);font-size:36px;line-height:46px;text-shadow:0 2px 4px rgba(0,0,0,.4)}
.hero-text{position:absolute;left:73px;top:456px;width:460px;color:var(--white);font-size:20px;line-height:34px}
.hero-btn{left:73px;top:553px;width:184px;height:46px;font-size:16px}
.dots{position:absolute;left:74px;top:809px;display:flex;gap:10px}
.dots span{width:10px;height:10px;border-radius:50%;background:#222}
.dots span:first-child{background:var(--white)}

/* welcome */
.welcome-text{position:absolute;left:150px;top:1040px;width:900px;text-align:center;font-size:15px;line-height:28px;color:var(--ink)}
.divider{position:absolute;left:73px;top:1305px;width:1052px;height:2px;background:#c8c8c8}

/* featured rows */
.feature{position:absolute;left:0;width:1200px;height:442px;background:var(--blue);overflow:hidden}
.feature-photo{position:absolute;top:0;height:442px}
.feature-copy{position:absolute;top:0;width:460px;color:var(--white)}
.feature-copy h3{font-size:30px;line-height:40px;margin-top:70px}
.feature-copy .price{font-size:32px;font-weight:700;margin-top:18px;line-height:40px}
.feature-copy p{font-size:13px;line-height:25px;margin-top:22px}
.feature-copy .btn{position:relative;width:148px;height:41px;margin-top:38px}

/* calendar section */
.calendar-band{position:absolute;left:0;top:2999px;width:1200px;height:641px;background:var(--light)}
.calendar{position:absolute;left:77px;top:3158px;width:509px;height:394px;background:var(--white);border:3px solid #a9d3ef;box-shadow:0 2px 8px rgba(0,0,0,.12)}
.cal-head{position:absolute;left:0;top:26px;width:100%;text-align:center;font-size:18px;color:var(--ink)}
.cal-arrow{position:absolute;top:26px;width:14px;height:14px;border-top:3px solid #333;border-left:3px solid #333}
.cal-grid{position:absolute;left:25px;top:72px;width:456px;display:grid;grid-template-columns:repeat(7,1fr);row-gap:0}
.cal-grid span{height:48px;display:flex;align-items:center;justify-content:center;font-size:16px;color:var(--ink)}
.cal-grid .dow{color:#777;font-size:15px;height:40px}
.cal-grid .link{color:var(--blue)}
.cal-grid .today{color:var(--white)}
.cal-grid .today i{font-style:normal;width:44px;height:44px;border-radius:50%;background:var(--navy);display:flex;align-items:center;justify-content:center}
.events{position:absolute;left:614px;top:3160px;width:511px}
.event{border-bottom:1px solid #cfcfcf;padding-bottom:10px;margin-bottom:18px}
.event:last-child{border-bottom:none}
.event .date{font-size:13px;font-weight:700;color:var(--blue)}
.event h4{font-size:17px;font-weight:400;color:var(--blue);margin-top:10px}
.event p{font-size:13px;line-height:24px;color:var(--muted);margin-top:4px}
.event p b{color:var(--blue);font-weight:400}

/* testimonials */
.testimonial{position:absolute;left:150px;top:3792px;width:902px;height:253px;background:var(--white);border-radius:10px;box-shadow:0 2px 14px rgba(0,0,0,.18)}
.stars{position:absolute;left:0;top:30px;width:100%;text-align:center;color:#f07a10;font-size:18px;letter-spacing:3px}
.quote{position:absolute;left:70px;top:62px;width:762px;text-align:center;font-size:15px;line-height:32px;color:#444}
.author{position:absolute;left:0;top:176px;width:100%;text-align:center;font-size:15px;font-weight:700;color:var(--blue);text-transform:uppercase}
.avatar{position:absolute;left:553px;top:3999px;width:96px;height:96px;border-radius:50%;background:linear-gradient(#cfd3d6,#8e959a);border:4px solid var(--white)}
.chev{position:absolute;top:3910px;width:14px;height:14px;border-top:3px solid #333;border-left:3px solid #333}

/* instagram */
.insta-band{position:absolute;left:0;top:4163px;width:1200px;height:351px;background:var(--lighter)}
.insta{position:absolute;top:4285px;width:250px;height:181px;background:linear-gradient(180deg,#9ea7ae 0%,#dfe4e8 60%,#f3f5f7 100%)}

/* newsletter */
.newsletter{position:absolute;left:0;top:4514px;width:1200px;height:113px;background:linear-gradient(90deg,#1167ab,#1e8fd6 55%,#2a9be0)}
.newsletter h2{position:absolute;left:125px;top:40px;color:var(--white);font-size:22px}
.newsletter .field{position:absolute;left:534px;top:32px;width:351px;height:47px;background:var(--white);font-size:12px;line-height:47px;padding-left:18px;color:#333}
.newsletter .btn{left:908px;top:32px;width:165px;height:47px;border:2px solid var(--white);background:transparent;font-size:14px}

/* footer */
.footer{position:absolute;left:0;top:4627px;width:1200px;height:315px;background:var(--footer);color:#bbb}
.footer-col{position:absolute;top:50px;font-size:13px;line-height:29px}
.footer-col h5{color:var(--white);font-size:16px;font-weight:400;text-transform:uppercase;margin-bottom:6px}
.contact-row{display:flex;gap:14px;line-height:21px;margin-bottom:12px}
.contact-row svg{flex:none;margin-top:3px}
.foot-socials{display:flex;gap:16px;margin-top:14px}
.foot-socials span{width:18px;height:18px;border-radius:50%;background:#8a8a8a}
.foot-brand{margin-top:18px;color:var(--blue);font-size:16px;font-weight:900;text-transform:uppercase;display:flex;align-items:center;gap:8px}
.foot-brand i{width:18px;height:18px;border-radius:50%;background:var(--blue)}
.copy{font-size:11px;line-height:20px;margin-top:14px}
</style>
</head>
<body>

<header class="hero">
  <div class="hero-photo" role="img" aria-label="Photo of a cyclist in a red jacket riding a blue fat tire bike on a snowy forest trail"></div>
  <div class="hero-panel"></div>
  <div class="brand">
    <div class="brand-mark"></div>
    <div class="brand-name">Tall Fern</div>
    <div class="brand-sub">Bicycle Rental</div>
    <div class="brand-tag">Great bikes for every trail</div>
  </div>
  <nav class="nav">
    <a class="active">Home</a><a>About Us</a><a>Rental Bicycle</a><a>Booking</a><a>Reviews</a><a>Blog</a><a>Contact Us</a>
  </nav>
  <div class="socials" aria-label="Social links"><span></span><span></span><span></span><span></span><span></span></div>
  <div class="btn login">Log In</div>
  <h1 class="hero-title display">Tall Fern Bicycle<br>Rental</h1>
  <p class="hero-text">Proin at urna placerat, hendrerit felis quis, varius diam fermentum viverra.</p>
  <div class="btn hero-btn">Book Your Ride</div>
  <div class="dots"><span></span><span></span><span></span><span></span></div>
</header>

<h2 class="section-title display" style="top:931px">Welcome to<br>Tall Fern Bicycle Rental</h2>
<p class="welcome-text">Lorem ipsum dolor sit amet, consectetur adipiscing elit. Proin at urna placerat, hendrerit felis quis, varius diam. Suspendisse potenti. Pellentesque nec sollicitudin nulla, non tincidunt lectus. Pellentesque quam quam, pharetra eu sagittis et, imperdiet vel enim. In dignissim, quam eu porttitor rutrum, eros ante sollicitudin mauris, sed posuere elit purus sit amet lacus.</p>
<div class="btn" style="left:526px;top:1194px;width:148px;height:39px;font-size:13px">Read More</div>
<div class="divider"></div>

<h2 class="section-title display" style="top:1344px">Featured<br>Bicycle Rental</h2>

<section class="feature" style="top:1486px">
  <div class="feature-photo" role="img" aria-label="Photo of a black fat tire bike with green rims parked on a snowy street" style="left:557px;width:643px;background:linear-gradient(135deg,#5d6266,#8f969b 50%,#c9ced1);clip-path:polygon(61px 0,100% 0,100% 100%,0 100%)"></div>
  <div class="feature-copy" style="left:77px">
    <h3 class="display">Heading Title</h3>
    <div class="price">$12.00/Day</div>
    <p>Lorem ipsum dolor sit amet, consectetur adipiscing elit. Phasellus condimentum ante sed turpis malesuada, feugiat scelerisque lectus viverra. Integer viverra congue nulla, ut congue lorem tincidunt id.</p>
    <div class="btn dark">Read More</div>
  </div>
</section>

<section class="feature" style="top:1928px">
  <div class="feature-photo" role="img" aria-label="Photo of a black and blue fat tire bike standing in snow among pine trees" style="left:0;width:665px;background:linear-gradient(180deg,#4d4a47,#8a8682 45%,#e7eaec);clip-path:polygon(0 0,610px 0,100% 100%,0 100%)"></div>
  <div class="feature-copy" style="left:705px">
    <h3 class="display">Heading Title</h3>
    <div class="price">$12.00/Day</div>
    <p>Lorem ipsum dolor sit amet, consectetur adipiscing elit. Phasellus condimentum ante sed turpis malesuada, feugiat scelerisque lectus viverra. Integer viverra congue nulla, ut congue lorem tincidunt id.</p>
    <div class="btn dark">Read More</div>
  </div>
</section>

<section class="feature" style="top:2369px">
  <div class="feature-photo" role="img" aria-label="Photo of a red fat tire bike on a dry grassy hillside under a blue sky" style="left:557px;width:643px;background:linear-gradient(180deg,#5f86b0,#9eb4c8 40%,#a58b5f 70%,#7b6a4b);clip-path:polygon(29px 0,100% 0,100% 100%,0 100%)"></div>
  <div class="feature-copy" style="left:77px">
    <h3 class="display">Heading Title</h3>
    <div class="price">$12.00/Day</div>
    <p>Lorem ipsum dolor sit amet, consectetur adipiscing elit. Phasellus condimentum ante sed turpis malesuada, feugiat scelerisque lectus viverra. Integer viverra congue nulla, ut congue lorem tincidunt id.</p>
    <div class="btn dark">Read More</div>
  </div>
</section>

<div class="btn" style="left:495px;top:2876px;width:210px;height:58px;font-size:20px">View All</div>

<div class="calendar-band"></div>
<h2 class="section-title display" style="top:3062px">Calendar</h2>
<div class="calendar">
  <span class="cal-arrow" style="left:37px;transform:rotate(-45deg)"></span>
  <div class="cal-head display" style="letter-spacing:1px">May 2020</div>
  <span class="cal-arrow" style="right:37px;transform:rotate(135deg)"></span>
  <div class="cal-grid">
    <span class="dow">S</span><span class="dow">M</span><span class="dow">T</span><span class="dow">W</span><span class="dow">T</span><span class="dow">F</span><span class="dow">S</span>
    <span></span><span></span><span></span><span></span><span></span><span></span><span>1</span>
    <span>2</span><span>3</span><span>4</span><span>5</span><span>6</span><span class="link">7</span><span>8</span>
    <span>9</span><span>10</span><span>11</span><span>12</span><span class="today"><i>13</i></span><span>14</span><span>15</span>
    <span>16</span><span>17</span><span>18</span><span>19</span><span>20</span><span>21</span><span>22</span>
    <span>23</span><span>24</span><span>25</span><span>26</span><span>27</span><span>28</span><span>29</span>
    <span>30</span>
  </div>
</div>
<div class="events">
  <div class="event">
    <div class="date">MAY28, 2020</div>
    <h4>Lorem ipsum dolor sit amet, consectetur adipiscing elit.</h4>
    <p>Phasellus condimentum ante sed turpis malesuada, feugiat scelerisque lectus fermentum viverra sapien. <b>[+]</b></p>
  </div>
  <div class="event">
    <div class="date">MAY28, 2020</div>
    <h4>Lorem ipsum dolor sit amet, consectetur adipiscing elit.</h4>
    <p>Phasellus condimentum ante sed turpis malesuada. <b>[+]</b></p>
  </div>
  <div class="event">
    <div class="date">MAY28, 2020</div>
    <h4>Lorem ipsum dolor sit amet, consectetur adipiscing elit.</h4>
    <p>Phasellus condimentum ante sed turpis malesuada. <b>[+]</b></p>
  </div>
</div>
<div class="btn" style="left:614px;top:3512px;width:181px;height:40px;font-size:14px">Book Your Ride</div>

<h2 class="section-title display" style="top:3702px">Testimonials</h2>
<span class="chev" style="left:168px;transform:rotate(-45deg)"></span>
<div class="testimonial">
  <div class="stars">★★★★★</div>
  <p class="quote">“ Pellentesque quam quam, pharetra eu sagittis et, imperdiet vel enim. In dignissim, quam eu porttitor rutrum, eros ante sollicitudin mauris, sed posuere elit purus sit amet lacus. Maecenas vel metus rhoncus odio bibendum sagittis....”</p>
  <div class="author">Dana Marsh</div>
</div>
<div class="avatar" role="img" aria-label="Portrait photo of the reviewer"></div>
<span class="chev" style="left:1022px;transform:rotate(135deg)"></span>

<div class="insta-band"></div>
<h2 class="section-title display" style="top:4211px;font-size:28px">Instagram</h2>
<div class="insta" style="left:73px" role="img" aria-label="Photo of a rider in blue on a fat tire bike in snowy woods"></div>
<div class="insta" style="left:342px" role="img" aria-label="Photo of a rider in a green jacket on a fat tire bike in snow"></div>
<div class="insta" style="left:609px" role="img" aria-label="Photo of two riders on fat tire bikes on a snowy trail"></div>
<div class="insta" style="left:877px" role="img" aria-label="Photo of a rider in red on a fat tire bike in a snowy field"></div>

<section class="newsletter">
  <h2 class="display">Newsletter Sign Up</h2>
  <div class="field">ENTER EMAIL ADDRESS</div>
  <div class="btn">Subscribe</div>
</section>

<footer class="footer">
  <div class="footer-col" style="left:77px">
    <h5>Sitemap</h5>
    Home<br>About Us<br>Rental Bicycle<br>Booking<br>Reviews<br>Blog<br>Contact Us
  </div>
  <div class="footer-col" style="left:328px">
    <h5>Help</h5>
    Etiam in vulputate<br>Odio et cursus<br>Anteaecenas<br>Luctus augue
  </div>
  <div class="footer-col" style="left:584px;width:270px">
    <h5>Contact Us</h5>
    <div class="contact-row">
      <svg width="12" height="16" viewBox="0 0 12 16"><path d="M6 0a6 6 0 0 0-6 6c0 4.5 6 10 6 10s6-5.5 6-10a6 6 0 0 0-6-6zm0 8.5A2.5 2.5 0 1 1 6 3.5a2.5 2.5 0 0 1 0 5z" fill="#bbb"/></svg>
      <span>Unit 4, 12 Birchwood Lane,<br>Pine Hollow,<br>Ridgefield 2210</span>
    </div>
    <div class="contact-row">
      <svg width="14" height="14" viewBox="0 0 14 14"><path d="M3 0l2.5 3.5-1.5 2a8 8 0 0 0 4.5 4.5l2-1.5L14 11l-2 3C5.5 13.5.5 8.5 0 2z" fill="#bbb"/></svg>
      <span>1-800-555-0142</span>
    </div>
    <div class="contact-row">
      <svg width="15" height="11" viewBox="0 0 15 11"><rect width="15" height="11" fill="#bbb"/><path d="M0 0l7.5 6L15 0" stroke="#262626" stroke-width="1.5" fill="none"/></svg>
      <span>hello@tallfernrental.com</span>
    </div>
  </div>
  <div class="footer-col" style="left:885px;width:240px">
    <h5>Follow Us</h5>
    <div class="foot-socials"><span></span><span></span><span></span><span></span><span></span></div>
    <div class="foot-brand"><i></i>Tall Fern</div>
    <div class="copy">Copyrights © 2020, Company Name<br>All rights reserved.</div>
  </div>
</footer>

</body>
</html>
```